TA BRAMLEY BUSINESS CARD DESIGN PROJECT

We need to utilize our logo that was expertly created on PixelHarbor and now need to match this with a business card design.

```html
<!DOCTYPE html>
<html lang="en">
<head>
<meta charset="utf-8">
<title>TA BRAMLEY – Business Card</title>
<link rel="stylesheet" href="https://fonts.googleapis.com/css2?family=Montserrat:wght@400;500;700&display=swap">
<style>
  :root {
    --stage: #474747;
    --card: #161616;
    --blue: #1158ad;
    --white: #ffffff;
    --emboss: #2b2b2b;
  }
  * { margin: 0; padding: 0; box-sizing: border-box; }
  html, body {
    width: 1200px;
    height: 801px;
    overflow: hidden;
    background: var(--stage);
    font-family: "Montserrat", sans-serif;
  }
  .card {
    position: absolute;
    top: 252px;
    width: 520px;
    height: 297px;
    background: var(--card);
    overflow: hidden;
    box-shadow: 0 10px 30px rgba(0,0,0,.35);
  }
  .card--front { left: 50px; }
  .card--back { left: 630px; }

  .card__swoosh { position: absolute; inset: 0; width: 100%; height: 100%; }

  .brand-name {
    position: absolute;
    font-weight: 700;
    letter-spacing: 0.08em;
    white-space: nowrap;
  }
  .card--front .brand-name {
    left: 38px;
    top: 136px;
    font-size: 21px;
    color: var(--blue);
  }
  .card--back .brand-name {
    left: 0;
    right: 0;
    top: 124px;
    text-align: center;
    font-size: 40px;
    color: var(--emboss);
  }

  .divider {
    position: absolute;
    left: 232px;
    top: 62px;
    width: 1.5px;
    height: 172px;
    background: var(--blue);
  }

  .contact {
    position: absolute;
    left: 254px;
    top: 58px;
    color: var(--white);
  }
  .contact__name {
    font-size: 17px;
    font-weight: 700;
    color: var(--blue);
    letter-spacing: 0.02em;
  }
  .contact__role {
    font-size: 12px;
    font-weight: 400;
    margin-bottom: 12px;
  }
  .contact__list { list-style: none; }
  .contact__item {
    display: flex;
    align-items: center;
    gap: 6px;
    font-size: 11.5px;
    line-height: 17px;
  }
  .contact__icon { width: 10px; height: 10px; flex: none; fill: var(--blue); }
  .contact__address {
    font-size: 11.5px;
    line-height: 16px;
    margin-top: 12px;
    font-style: normal;
  }
</style>
</head>
<body>

<section class="card card--front">
  <svg class="card__swoosh" viewBox="0 0 520 297" aria-hidden="true">
    <path d="M0,0 H190 C120,20 50,45 0,68 Z" fill="var(--blue)"/>
    <path d="M212,0 C130,22 60,48 0,78" fill="none" stroke="var(--blue)" stroke-width="2.5"/>
    <path d="M520,297 H355 C420,282 480,258 520,232 Z" fill="var(--blue)"/>
    <path d="M330,297 C405,282 470,256 520,222" fill="none" stroke="var(--blue)" stroke-width="2.5"/>
  </svg>

  <div class="brand-name">TA BRAMLEY</div>

  <div class="divider"></div>

  <div class="contact">
    <h1 class="contact__name">MARCUS HALE</h1>
    <p class="contact__role">Managing Director</p>
    <ul class="contact__list">
      <li class="contact__item">
        <svg class="contact__icon" viewBox="0 0 10 10"><path d="M2 0.5 L3.8 2.6 L2.9 3.8 C3.6 5.2 4.8 6.4 6.2 7.1 L7.4 6.2 L9.5 8 L8.4 9.5 C4.5 9.2 0.8 5.5 0.5 1.6 Z"/></svg>
        123 456 789
      </li>
      <li class="contact__item">
        <svg class="contact__icon" viewBox="0 0 10 10"><rect x="2" y="0.5" width="6" height="3"/><rect x="0.5" y="3.5" width="9" height="4.5" rx="0.8"/><rect x="2" y="7" width="6" height="2.5"/></svg>
        123 456 789
      </li>
      <li class="contact__item">
        <svg class="contact__icon" viewBox="0 0 10 10"><path d="M0.5 2 H9.5 V8.5 H0.5 Z M0.5 2 L5 5.5 L9.5 2" stroke="var(--card)" stroke-width="0.8"/></svg>
        info@yourgmail.com
      </li>
      <li class="contact__item">
        <svg class="contact__icon" viewBox="0 0 10 10"><circle cx="5" cy="5" r="4.5"/><path d="M0.5 5 H9.5 M5 0.5 C3 3 3 7 5 9.5 M5 0.5 C7 3 7 7 5 9.5" fill="none" stroke="var(--card)" stroke-width="0.7"/></svg>
        www.yourwebsite.com
      </li>
    </ul>
    <address class="contact__address">
      Your address, City<br>
      State, Zip 1234
    </address>
  </div>
</section>

<section class="card card--back">
  <div class="brand-name">TA BRAMLEY</div>
</section>

</body>
</html>
```